Business Card for Professional Photographer

I'm looking for an eye catching modern clean design that compliments my logo/ website fonts & colours.
I specialise in architecture, corporate & commercial photography so I'm marketing to professional clients rather than portrait / wedding clients.

I would prefer to not have a solid black design.

My logo brand guide is as follows :

Main front font. : Reislust
Main font colour : #fff
Slogan front font : Ubuntu Bold
Monogram front font : Venti Medium
Container colour : #fff

I need print ready files in pdf .png & .eps formats.

Included in the files below are some screen grabs as reference to font & colours etc.

```html
<!DOCTYPE html>
<html lang="en">
<head>
<meta charset="utf-8">
<title>Lens and Line – Business Card</title>
<link rel="stylesheet" href="https://fonts.googleapis.com/css2?family=Ubuntu:wght@400;500;700&display=swap">
<style>
  :root {
    --backdrop: #545454;
    --paper: #ffffff;
    --gold: #cf9f5f;
    --gold-light: #dfba7f;
    --gold-deep: #cd9d5e;
    --ink: #4a4a4a;
    --ink-strong: #3a3a3a;
    --white: #ffffff;
  }
  * { margin: 0; padding: 0; box-sizing: border-box; }
  html, body { width: 963px; height: 1200px; overflow: hidden; }
  body {
    background: var(--backdrop);
    font-family: "Ubuntu", sans-serif;
    position: relative;
  }
  .card {
    position: absolute;
    left: 232px;
    width: 557px;
    height: 318px;
  }
  .card--front { top: 222px; background: var(--paper); }
  .card--back {
    top: 636px;
    height: 320px;
    background: linear-gradient(180deg, var(--gold-light) 0%, var(--gold-deep) 100%);
  }

  .line {
    position: absolute;
    left: 31px;
    color: var(--ink);
    font-size: 12.5px;
    line-height: 16px;
    white-space: nowrap;
  }
  .line--name { top: 31px; color: var(--gold); font-size: 18.5px; font-weight: 500; line-height: 22px; }
  .line--role { top: 53px; color: var(--ink-strong); font-weight: 500; }
  .line--email { top: 70px; }
  .line--rule { top: 100px; letter-spacing: 0.5px; }
  .line--tel { top: 137px; }
  .line--mob { top: 153px; }
  .line--fax { top: 168px; }
  .line--rule-second { top: 200px; left: 35px; letter-spacing: 0.5px; }
  .line--street { top: 233px; }
  .line--city { top: 249px; }
  .line--web { top: 266px; }

  .front-mark {
    position: absolute;
    left: 254px;
    top: 47px;
    width: 267px;
    height: 223px;
    display: flex;
    align-items: center;
    justify-content: center;
    color: var(--gold);
    font-size: 30px;
    font-weight: 500;
  }

  .brand {
    position: absolute;
    left: 119px;
    top: 141px;
    display: flex;
    align-items: center;
    gap: 14px;
    color: var(--white);
  }
  .brand__square { width: 12px; height: 12px; background: var(--white); }
  .brand__name { font-size: 20px; font-weight: 500; line-height: 22px; }
  .brand__tagline { font-size: 8px; font-weight: 500; letter-spacing: 1px; margin-top: 4px; }
</style>
</head>
<body>
  <section class="card card--front">
    <p class="line line--name">Daniel Hart</p>
    <p class="line line--role">President</p>
    <p class="line line--email">hello@lensandline.com</p>
    <p class="line line--rule">..............</p>
    <p class="line line--tel">tel . 555-214-7390</p>
    <p class="line line--mob">mob. 555-618-2045</p>
    <p class="line line--fax">fax. 555-307-9182</p>
    <p class="line line--rule-second">..............</p>
    <p class="line line--street">412 Cedar Ridge Road</p>
    <p class="line line--city">Fairbanks, Alaska 34512</p>
    <p class="line line--web">www.lensandline.com</p>
    <p class="front-mark">Lens and Line</p>
  </section>

  <section class="card card--back">
    <div class="brand">
      <span class="brand__square" aria-hidden="true"></span>
      <div>
        <p class="brand__name">Lens and Line</p>
        <p class="brand__tagline">Buildings Brands Business Imagery</p>
      </div>
    </div>
  </section>
</body>
</html>
```